sydney wedding photography business needs a business card design

we need a business card design for a sydney based wedding photography and videography business. our business name is :golden hour studio and film. our target clients are 24-35 yrs female. our style is candid, organic, natural, dynamic. we are a team of young photographers and videographers, and help brides to create memories that they will cherish for the rest of their lives. the logo will be provided. we want an elegant design that reflects our style, and also want to give a great impression to our clients that we are one of the best studios in sydney and our brand means quality and premium service.

Target Market(s)

bride to be, 24-35 years old, living in sydney and surrunding areas

Industry/Entity Type

Wedding Photography

Contact Information for Business Card

address: 57 tarrant street, glenmore nsw 2047
mobile: 0431872259
phone: (02) 9163 2408
info@tidewillowstudio.net.au
www.tidewillowstudio.net.au
facebook:tidewillowweddings
instagram:tidewillowweddings

Font styles to use
Serif
Sans Serif

Requirements
Nice to have
• maybe add my slogan"memories beyond eternity" if the layout looks good
Should not have
• no black color, not good idea for wedding biz card

```html
<!DOCTYPE html>
<html lang="en">
<head>
<meta charset="utf-8">
<title>Golden Hour Studio and Film — Business Card</title>
<link rel="stylesheet" href="https://fonts.googleapis.com/css2?family=Josefin+Sans:wght@400;600&family=Montserrat:wght@400&display=swap">
<style>
  :root {
    --backdrop: #4a4642;
    --gold-light: #e8d585;
    --gold: #cdb560;
    --gold-deep: #ad9444;
    --panel: #6a6360;
    --panel-deep: #554f4c;
    --photo-light: #9a948e;
    --photo-mid: #78726d;
    --photo-deep: #5c5652;
    --ink-light: #fbf8f1;
    --icon-mark: #5c5652;
  }
  * { margin: 0; padding: 0; box-sizing: border-box; }
  html, body { width: 1200px; height: 922px; overflow: hidden; }
  body { background: var(--backdrop); position: relative; }

  .card {
    position: absolute;
    width: 640px;
    height: 366px;
    border-radius: 16px;
    overflow: hidden;
    box-shadow: 0 12px 30px rgba(40,34,30,0.45);
  }

  /* Front */
  .card-front { left: 60px; top: 60px; }
  .front-pattern {
    position: absolute; inset: 0;
    background:
      radial-gradient(circle at 30% 25%, rgba(255,248,210,0.35), transparent 55%),
      linear-gradient(135deg, var(--gold-light), var(--gold) 55%, var(--gold-deep));
  }
  .front-frame {
    position: absolute;
    left: 110px; top: 80px; width: 420px; height: 206px;
    border: 10px solid var(--gold-light);
    background: linear-gradient(160deg, var(--panel), var(--panel-deep));
    display: flex; flex-direction: column; align-items: center; justify-content: center;
  }
  .brand-name {
    font-family: "Josefin Sans", sans-serif;
    font-weight: 600;
    color: var(--gold-light);
    text-transform: uppercase;
    letter-spacing: 0.18em;
    text-align: center;
    line-height: 1.3;
  }
  .front-frame .brand-name { font-size: 28px; }

  /* Back */
  .card-back { left: 500px; top: 496px; }
  .back-photo {
    position: absolute; inset: 0;
    background:
      radial-gradient(ellipse at 58% 60%, var(--photo-light), transparent 60%),
      linear-gradient(150deg, var(--photo-mid), var(--photo-deep));
  }
  .card-back .brand-name {
    position: absolute; right: 34px; top: 40px;
    font-size: 26px; text-align: right;
  }
  .contact-list {
    position: absolute; left: 30px; bottom: 28px;
    list-style: none;
    font-family: "Montserrat", sans-serif;
    font-size: 18px;
    color: var(--ink-light);
    text-shadow: 0 1px 2px rgba(60,52,48,0.6);
  }
  .contact-item { display: flex; align-items: center; gap: 12px; height: 28px; white-space: nowrap; }
  .contact-icon { width: 18px; height: 18px; flex: none; }
  .contact-icon rect.bg { fill: var(--gold); }
  .contact-icon .mark { fill: none; stroke: var(--icon-mark); stroke-width: 1.4; stroke-linecap: round; stroke-linejoin: round; }
</style>
</head>
<body>

<section class="card card-front" aria-label="Business card front">
  <div class="front-pattern" role="img" aria-label="Gold card surface with a scattered diamond pattern"></div>
  <div class="front-frame">
    <p class="brand-name">Golden Hour<br>Studio and Film</p>
  </div>
</section>

<section class="card card-back" aria-label="Business card back">
  <div class="back-photo" role="img" aria-label="Soft monochrome wedding photograph of a couple in an ornate doorway"></div>
  <p class="brand-name">Golden Hour<br>Studio and Film</p>

  <ul class="contact-list">
    <li class="contact-item">
      <svg class="contact-icon" viewBox="0 0 17 17"><rect class="bg" width="17" height="17" rx="2"/><path class="mark" d="M5 4l2 0 1 3-1.5 1a6 6 0 0 0 2.5 2.5l1-1.5 3 1v2a1 1 0 0 1-1 1A8 8 0 0 1 4 5a1 1 0 0 1 1-1z"/></svg>
      <span>(02) 9163 2408</span>
    </li>
    <li class="contact-item">
      <svg class="contact-icon" viewBox="0 0 17 17"><rect class="bg" width="17" height="17" rx="2"/><rect class="mark" x="5.5" y="3" width="6" height="11" rx="1"/><path class="mark" d="M8 12h1"/></svg>
      <span>0431872259</span>
    </li>
    <li class="contact-item">
      <svg class="contact-icon" viewBox="0 0 17 17"><rect class="bg" width="17" height="17" rx="2"/><circle class="mark" cx="8.5" cy="8.5" r="5"/><path class="mark" d="M3.5 8.5h10M8.5 3.5c-2.5 3-2.5 7 0 10M8.5 3.5c2.5 3 2.5 7 0 10"/></svg>
      <span>www.tidewillowstudio.net.au</span>
    </li>
    <li class="contact-item">
      <svg class="contact-icon" viewBox="0 0 17 17"><rect class="bg" width="17" height="17" rx="2"/><rect class="mark" x="3" y="5" width="11" height="7.5"/><path class="mark" d="M3 5l5.5 4.5L14 5"/></svg>
      <span>info@tidewillowstudio.net.au</span>
    </li>
    <li class="contact-item">
      <svg class="contact-icon" viewBox="0 0 17 17"><rect class="bg" width="17" height="17" rx="2"/></svg>
      <span>tidewillowweddings</span>
    </li>
    <li class="contact-item">
      <svg class="contact-icon" viewBox="0 0 17 17"><rect class="bg" width="17" height="17" rx="2"/></svg>
      <span>tidewillowweddings</span>
    </li>
    <li class="contact-item">
      <svg class="contact-icon" viewBox="0 0 17 17"><rect class="bg" width="17" height="17" rx="2"/><path class="mark" d="M8.5 14s-4-4-4-7a4 4 0 0 1 8 0c0 3-4 7-4 7z"/><circle class="mark" cx="8.5" cy="7" r="1.4"/></svg>
      <span>57 tarrant street, glenmore nsw 2047</span>
    </li>
  </ul>
</section>

</body>
</html>
```